Hallowell Kin Playing Cards

We are wanting a cool design for a playing card that includes our logo(s). I will attach our two logos, we are open to using either one of them or another version of them. I will also attach some pictures of card decks to use for inspiration. These are just decks that we have seen from other artists that we liked. We are located in West Texas so although not necessary, a Sotol or Agave or cactus or quail (bird) or some sort of sunset would pay homage to our surroundings. I realize the examples are all very different, but those are just some decks that we like! Thank you!

```html
<!DOCTYPE html>
<html lang="en">
<head>
<meta charset="utf-8">
<title>Hallowell Kin Playing Cards – Deck Layout</title>
<link rel="stylesheet" href="https://fonts.googleapis.com/css2?family=Alfa+Slab+One&display=swap">
<style>
  :root {
    --paper: #ffffff;
    --card: #070a0c;
    --card-edge: #c9cdd0;
    --red: #e0212b;
    --red-art: #8e1a20;
    --ivory: #f2f2f2;
    --ivory-art: #6f7376;
    --back-light: #2a8fd6;
    --back-dark: #0c4f8c;
  }
  html, body {
    margin: 0;
    padding: 0;
    width: 1200px;
    height: 546px;
    overflow: hidden;
    background: var(--paper);
  }
  .deck-sheet { display: block; width: 1200px; height: 546px; }
  .card-body { fill: var(--card); stroke: var(--card-edge); stroke-width: .7; }
  .card-inner { fill: none; stroke: #e8e8e8; stroke-width: .35; }
  .idx { font-family: "Alfa Slab One", Georgia, serif; font-size: 8px; }
  .joker-idx { font-family: "Alfa Slab One", Georgia, serif; font-size: 4px; }
  .hearts, .diamonds { fill: var(--red); }
  .spades, .clubs { fill: var(--ivory); }
  .hearts .pips, .hearts .idx-pip { fill: url(#pip-heart); }
  .diamonds .pips, .diamonds .idx-pip { fill: url(#pip-diamond); }
  .spades .pips, .spades .idx-pip { fill: url(#pip-spade); }
  .clubs .pips, .clubs .idx-pip { fill: url(#pip-club); }
  .art-red { fill: var(--red-art); }
  .art-ivory { fill: var(--ivory-art); }
  .ink-red { fill: var(--red); }
  .ink-ivory { fill: var(--ivory); }
  .back-art { fill: url(#back-gradient); }
  .back-name { font-family: "Alfa Slab One", Georgia, serif; font-size: 5px; fill: #ffffff; }
</style>
</head>
<body>
<svg class="deck-sheet" viewBox="0 0 1200 546" xmlns="http://www.w3.org/2000/svg">
  <defs>
    <pattern id="pip-heart" patternUnits="objectBoundingBox" patternContentUnits="objectBoundingBox" width="1" height="1">
      <rect width="1" height="1" fill="var(--card)"/>
      <path class="ink-red" d="M.5 .95C.1 .6 0 .45 0 .28C0 .1 .15 0 .28 0C.4 0 .47 .08 .5 .17C.53 .08 .6 0 .72 0C.85 0 1 .1 1 .28C1 .45 .9 .6 .5 .95Z"/>
    </pattern>
    <pattern id="pip-diamond" patternUnits="objectBoundingBox" patternContentUnits="objectBoundingBox" width="1" height="1">
      <rect width="1" height="1" fill="var(--card)"/>
      <path class="ink-red" d="M.5 0L.88 .5L.5 1L.12 .5Z"/>
    </pattern>
    <pattern id="pip-spade" patternUnits="objectBoundingBox" patternContentUnits="objectBoundingBox" width="1" height="1">
      <rect width="1" height="1" fill="var(--card)"/>
      <path class="ink-ivory" d="M.5 0C.1 .35 0 .5 0 .65C0 .82 .15 .9 .28 .9C.38 .9 .45 .84 .48 .78L.4 1H.6L.52 .78C.55 .84 .62 .9 .72 .9C.85 .9 1 .82 1 .65C1 .5 .9 .35 .5 0Z"/>
    </pattern>
    <pattern id="pip-club" patternUnits="objectBoundingBox" patternContentUnits="objectBoundingBox" width="1" height="1">
      <rect width="1" height="1" fill="var(--card)"/>
      <g class="ink-ivory">
        <circle cx=".5" cy=".27" r=".22"/>
        <circle cx=".26" cy=".6" r=".22"/>
        <circle cx=".74" cy=".6" r=".22"/>
        <path d="M.46 .55L.38 1H.62L.54 .55Z"/>
      </g>
    </pattern>
    <linearGradient id="back-gradient" x1="0" y1="0" x2="1" y2="1">
      <stop offset="0" stop-color="#2a8fd6"/>
      <stop offset="1" stop-color="#0c4f8c"/>
    </linearGradient>

    <g id="card-face">
      <rect class="card-body" width="66" height="92" rx="1.6"/>
      <rect class="card-inner" x="2" y="2" width="62" height="88" rx="1"/>
    </g>

    <g id="layout-10">
      <rect x="16" y="8" width="11" height="11"/><rect x="37.5" y="8" width="11" height="11"/>
      <rect x="26.75" y="18.5" width="11" height="11"/>
      <rect x="16" y="29.5" width="11" height="11"/><rect x="37.5" y="29.5" width="11" height="11"/>
      <rect x="16" y="51.5" width="11" height="11"/><rect x="37.5" y="51.5" width="11" height="11"/>
      <rect x="26.75" y="62.5" width="11" height="11"/>
      <rect x="16" y="73" width="11" height="11"/><rect x="37.5" y="73" width="11" height="11"/>
    </g>
    <g id="layout-9">
      <rect x="16" y="8" width="11" height="11"/><rect x="37.5" y="8" width="11" height="11"/>
      <rect x="16" y="29.5" width="11" height="11"/><rect x="37.5" y="29.5" width="11" height="11"/>
      <rect x="26.75" y="41.5" width="11" height="11"/>
      <rect x="16" y="51.5" width="11" height="11"/><rect x="37.5" y="51.5" width="11" height="11"/>
      <rect x="16" y="73" width="11" height="11"/><rect x="37.5" y="73" width="11" height="11"/>
    </g>
    <g id="layout-8">
      <rect x="16" y="8" width="11" height="11"/><rect x="37.5" y="8" width="11" height="11"/>
      <rect x="16" y="29.5" width="11" height="11"/><rect x="37.5" y="29.5" width="11" height="11"/>
      <rect x="16" y="51.5" width="11" height="11"/><rect x="37.5" y="51.5" width="11" height="11"/>
      <rect x="16" y="73" width="11" height="11"/><rect x="37.5" y="73" width="11" height="11"/>
    </g>
    <g id="layout-7">
      <rect x="16" y="8" width="11" height="11"/><rect x="37.5" y="8" width="11" height="11"/>
      <rect x="26.75" y="23.5" width="11" height="11"/>
      <rect x="16" y="39.5" width="11" height="11"/><rect x="37.5" y="39.5" width="11" height="11"/>
      <rect x="16" y="73" width="11" height="11"/><rect x="37.5" y="73" width="11" height="11"/>
    </g>
    <g id="layout-6">
      <rect x="16" y="8" width="11" height="11"/><rect x="37.5" y="8" width="11" height="11"/>
      <rect x="16" y="39.5" width="11" height="11"/><rect x="37.5" y="39.5" width="11" height="11"/>
      <rect x="16" y="73" width="11" height="11"/><rect x="37.5" y="73" width="11" height="11"/>
    </g>
    <g id="layout-5">
      <rect x="16" y="8" width="11" height="11"/><rect x="37.5" y="8" width="11" height="11"/>
      <rect x="26.75" y="39.5" width="11" height="11"/>
      <rect x="16" y="73" width="11" height="11"/><rect x="37.5" y="73" width="11" height="11"/>
    </g>
    <g id="layout-4">
      <rect x="16" y="8" width="11" height="11"/><rect x="37.5" y="8" width="11" height="11"/>
      <rect x="16" y="73" width="11" height="11"/><rect x="37.5" y="73" width="11" height="11"/>
    </g>
    <g id="layout-3">
      <rect x="26.75" y="8" width="11" height="11"/>
      <rect x="26.75" y="39.5" width="11" height="11"/>
      <rect x="26.75" y="73" width="11" height="11"/>
    </g>
    <g id="layout-2">
      <rect x="26.75" y="8" width="11" height="11"/>
      <rect x="26.75" y="73" width="11" height="11"/>
    </g>
  </defs>

  <!-- Hearts row -->
  <g class="suit-row hearts">
    <g class="card joker" transform="translate(36,35)">
      <use href="#card-face"/>
      <text class="joker-idx" x="3.5" y="6"><tspan x="3.5">J</tspan><tspan x="3.5" dy="4">O</tspan><tspan x="3.5" dy="4">K</tspan><tspan x="3.5" dy="4">E</tspan><tspan x="3.5" dy="4">R</tspan></text>
      <g transform="rotate(180 33 46)"><text class="joker-idx" x="3.5" y="6"><tspan x="3.5">J</tspan><tspan x="3.5" dy="4">O</tspan><tspan x="3.5" dy="4">K</tspan><tspan x="3.5" dy="4">E</tspan><tspan x="3.5" dy="4">R</tspan></text></g>
      <rect class="art-red" x="10" y="24" width="44" height="38" rx="3" role="img" aria-label="Red jester hat illustration"/>
    </g>
    <g class="card" transform="translate(114.6,35)">
      <use href="#card-face"/>
      <text class="idx" x="3.5" y="10">A</text><rect class="idx-pip" x="3.5" y="12" width="5" height="5"/>
      <g transform="rotate(180 33 46)"><text class="idx" x="3.5" y="10">A</text><rect class="idx-pip" x="3.5" y="12" width="5" height="5"/></g>
      <rect class="art-red" x="15" y="24" width="36" height="42" rx="4" role="img" aria-label="Ornate filigree heart, ace of hearts illustration"/>
    </g>
    <g class="card" transform="translate(193.2,35)">
      <use href="#card-face"/>
      <text class="idx" x="3.5" y="10">K</text><rect class="idx-pip" x="3.5" y="12" width="5" height="5"/>
      <g transform="rotate(180 33 46)"><text class="idx" x="3.5" y="10">K</text><rect class="idx-pip" x="3.5" y="12" width="5" height="5"/></g>
      <rect class="art-red" x="11" y="8" width="44" height="76" rx="2" role="img" aria-label="King of hearts court illustration"/>
    </g>
    <g class="card" transform="translate(271.8,35)">
      <use href="#card-face"/>
      <text class="idx" x="3.5" y="10">Q</text><rect class="idx-pip" x="3.5" y="12" width="5" height="5"/>
      <g transform="rotate(180 33 46)"><text class="idx" x="3.5" y="10">Q</text><rect class="idx-pip" x="3.5" y="12" width="5" height="5"/></g>
      <rect class="art-red" x="11" y="8" width="44" height="76" rx="2" role="img" aria-label="Queen of hearts court illustration"/>
    </g>
    <g class="card" transform="translate(350.4,35)">
      <use href="#card-face"/>
      <text class="idx" x="3.5" y="10">J</text><rect class="idx-pip" x="3.5" y="12" width="5" height="5"/>
      <g transform="rotate(180 33 46)"><text class="idx" x="3.5" y="10">J</text><rect class="idx-pip" x="3.5" y="12" width="5" height="5"/></g>
      <rect class="art-red" x="11" y="8" width="44" height="76" rx="2" role="img" aria-label="Jack of hearts court illustration"/>
    </g>
    <g class="card" transform="translate(429,35)"><use href="#card-face"/><text class="idx" x="2.5" y="10">10</text><rect class="idx-pip" x="3.5" y="12" width="5" height="5"/><g transform="rotate(180 33 46)"><text class="idx" x="2.5" y="10">10</text><rect class="idx-pip" x="3.5" y="12" width="5" height="5"/></g><use class="pips" href="#layout-10"/></g>
    <g class="card" transform="translate(507.6,35)"><use href="#card-face"/><text class="idx" x="3.5" y="10">9</text><rect class="idx-pip" x="3.5" y="12" width="5" height="5"/><g transform="rotate(180 33 46)"><text class="idx" x="3.5" y="10">9</text><rect class="idx-pip" x="3.5" y="12" width="5" height="5"/></g><use class="pips" href="#layout-9"/></g>
    <g class="card" transform="translate(586.2,35)"><use href="#card-face"/><text class="idx" x="3.5" y="10">8</text><rect class="idx-pip" x="3.5" y="12" width="5" height="5"/><g transform="rotate(180 33 46)"><text class="idx" x="3.5" y="10">8</text><rect class="idx-pip" x="3.5" y="12" width="5" height="5"/></g><use class="pips" href="#layout-8"/></g>
    <g class="card" transform="translate(664.8,35)"><use href="#card-face"/><text class="idx" x="3.5" y="10">7</text><rect class="idx-pip" x="3.5" y="12" width="5" height="5"/><g transform="rotate(180 33 46)"><text class="idx" x="3.5" y="10">7</text><rect class="idx-pip" x="3.5" y="12" width="5" height="5"/></g><use class="pips" href="#layout-7"/></g>
    <g class="card" transform="translate(743.4,35)"><use href="#card-face"/><text class="idx" x="3.5" y="10">6</text><rect class="idx-pip" x="3.5" y="12" width="5" height="5"/><g transform="rotate(180 33 46)"><text class="idx" x="3.5" y="10">6</text><rect class="idx-pip" x="3.5" y="12" width="5" height="5"/></g><use class="pips" href="#layout-6"/></g>
    <g class="card" transform="translate(822,35)"><use href="#card-face"/><text class="idx" x="3.5" y="10">5</text><rect class="idx-pip" x="3.5" y="12" width="5" height="5"/><g transform="rotate(180 33 46)"><text class="idx" x="3.5" y="10">5</text><rect class="idx-pip" x="3.5" y="12" width="5" height="5"/></g><use class="pips" href="#layout-5"/></g>
    <g class="card" transform="translate(900.6,35)"><use href="#card-face"/><text class="idx" x="3.5" y="10">4</text><rect class="idx-pip" x="3.5" y="12" width="5" height="5"/><g transform="rotate(180 33 46)"><text class="idx" x="3.5" y="10">4</text><rect class="idx-pip" x="3.5" y="12" width="5" height="5"/></g><use class="pips" href="#layout-4"/></g>
    <g class="card" transform="translate(979.2,35)"><use href="#card-face"/><text class="idx" x="3.5" y="10">3</text><rect class="idx-pip" x="3.5" y="12" width="5" height="5"/><g transform="rotate(180 33 46)"><text class="idx" x="3.5" y="10">3</text><rect class="idx-pip" x="3.5" y="12" width="5" height="5"/></g><use class="pips" href="#layout-3"/></g>
    <g class="card" transform="translate(1057.8,35)"><use href="#card-face"/><text class="idx" x="3.5" y="10">2</text><rect class="idx-pip" x="3.5" y="12" width="5" height="5"/><g transform="rotate(180 33 46)"><text class="idx" x="3.5" y="10">2</text><rect class="idx-pip" x="3.5" y="12" width="5" height="5"/></g><use class="pips" href="#layout-2"/></g>
  </g>

  <!-- Spades row -->
  <g class="suit-row spades">
    <g class="card card-back" transform="translate(36,144)">
      <rect class="card-body" width="66" height="92" rx="1.6"/>
      <rect class="back-art" x="1" y="1" width="64" height="90" rx="1.2" role="img" aria-label="Blue ornamental card back pattern"/>
      <text class="back-name" x="33" y="48" text-anchor="middle">HALLOWELL KIN</text>
    </g>
    <g class="card" transform="translate(114.6,144)">
      <use href="#card-face"/>
      <text class="idx" x="3.5" y="10">A</text><rect class="idx-pip" x="3.5" y="12" width="5" height="5"/>
      <g transform="rotate(180 33 46)"><text class="idx" x="3.5" y="10">A</text><rect class="idx-pip" x="3.5" y="12" width="5" height="5"/></g>
      <rect class="art-ivory" x="15" y="22" width="36" height="46" rx="4" role="img" aria-label="Ornate filigree spade, ace of spades illustration"/>
    </g>
    <g class="card" transform="translate(193.2,144)">
      <use href="#card-face"/>
      <text class="idx" x="3.5" y="10">K</text><rect class="idx-pip" x="3.5" y="12" width="5" height="5"/>
      <g transform="rotate(180 33 46)"><text class="idx" x="3.5" y="10">K</text><rect class="idx-pip" x="3.5" y="12" width="5" height="5"/></g>
      <rect class="art-ivory" x="11" y="8" width="44" height="76" rx="2" role="img" aria-label="King of spades court illustration"/>
    </g>
    <g class="card" transform="translate(271.8,144)">
      <use href="#card-face"/>
      <text class="idx" x="3.5" y="10">Q</text><rect class="idx-pip" x="3.5" y="12" width="5" height="5"/>
      <g transform="rotate(180 33 46)"><text class="idx" x="3.5" y="10">Q</text><rect class="idx-pip" x="3.5" y="12" width="5" height="5"/></g>
      <rect class="art-ivory" x="11" y="8" width="44" height="76" rx="2" role="img" aria-label="Queen of spades court illustration"/>
    </g>
    <g class="card" transform="translate(350.4,144)">
      <use href="#card-face"/>
      <text class="idx" x="3.5" y="10">J</text><rect class="idx-pip" x="3.5" y="12" width="5" height="5"/>
      <g transform="rotate(180 33 46)"><text class="idx" x="3.5" y="10">J</text><rect class="idx-pip" x="3.5" y="12" width="5" height="5"/></g>
      <rect class="art-ivory" x="11" y="8" width="44" height="76" rx="2" role="img" aria-label="Jack of spades court illustration"/>
    </g>
    <g class="card" transform="translate(429,144)"><use href="#card-face"/><text class="idx" x="2.5" y="10">10</text><rect class="idx-pip" x="3.5" y="12" width="5" height="5"/><g transform="rotate(180 33 46)"><text class="idx" x="2.5" y="10">10</text><rect class="idx-pip" x="3.5" y="12" width="5" height="5"/></g><use class="pips" href="#layout-10"/></g>
    <g class="card" transform="translate(507.6,144)"><use href="#card-face"/><text class="idx" x="3.5" y="10">9</text><rect class="idx-pip" x="3.5" y="12" width="5" height="5"/><g transform="rotate(180 33 46)"><text class="idx" x="3.5" y="10">9</text><rect class="idx-pip" x="3.5" y="12" width="5" height="5"/></g><use class="pips" href="#layout-9"/></g>
    <g class="card" transform="translate(586.2,144)"><use href="#card-face"/><text class="idx" x="3.5" y="10">8</text><rect class="idx-pip" x="3.5" y="12" width="5" height="5"/><g transform="rotate(180 33 46)"><text class="idx" x="3.5" y="10">8</text><rect class="idx-pip" x="3.5" y="12" width="5" height="5"/></g><use class="pips" href="#layout-8"/></g>
    <g class="card" transform="translate(664.8,144)"><use href="#card-face"/><text class="idx" x="3.5" y="10">7</text><rect class="idx-pip" x="3.5" y="12" width="5" height="5"/><g transform="rotate(180 33 46)"><text class="idx" x="3.5" y="10">7</text><rect class="idx-pip" x="3.5" y="12" width="5" height="5"/></g><use class="pips" href="#layout-7"/></g>
    <g class="card" transform="translate(743.4,144)"><use href="#card-face"/><text class="idx" x="3.5" y="10">6</text><rect class="idx-pip" x="3.5" y="12" width="5" height="5"/><g transform="rotate(180 33 46)"><text class="idx" x="3.5" y="10">6</text><rect class="idx-pip" x="3.5" y="12" width="5" height="5"/></g><use class="pips" href="#layout-6"/></g>
    <g class="card" transform="translate(822,144)"><use href="#card-face"/><text class="idx" x="3.5" y="10">5</text><rect class="idx-pip" x="3.5" y="12" width="5" height="5"/><g transform="rotate(180 33 46)"><text class="idx" x="3.5" y="10">5</text><rect class="idx-pip" x="3.5" y="12" width="5" height="5"/></g><use class="pips" href="#layout-5"/></g>
    <g class="card" transform="translate(900.6,144)"><use href="#card-face"/><text class="idx" x="3.5" y="10">4</text><rect class="idx-pip" x="3.5" y="12" width="5" height="5"/><g transform="rotate(180 33 46)"><text class="idx" x="3.5" y="10">4</text><rect class="idx-pip" x="3.5" y="12" width="5" height="5"/></g><use class="pips" href="#layout-4"/></g>
    <g class="card" transform="translate(979.2,144)"><use href="#card-face"/><text class="idx" x="3.5" y="10">3</text><rect class="idx-pip" x="3.5" y="12" width="5" height="5"/><g transform="rotate(180 33 46)"><text class="idx" x="3.5" y="10">3</text><rect class="idx-pip" x="3.5" y="12" width="5" height="5"/></g><use class="pips" href="#layout-3"/></g>
    <g class="card" transform="translate(1057.8,144)"><use href="#card-face"/><text class="idx" x="3.5" y="10">2</text><rect class="idx-pip" x="3.5" y="12" width="5" height="5"/><g transform="rotate(180 33 46)"><text class="idx" x="3.5" y="10">2</text><rect class="idx-pip" x="3.5" y="12" width="5" height="5"/></g><use class="pips" href="#layout-2"/></g>
  </g>

  <!-- Diamonds row -->
  <g class="suit-row diamonds">
    <g class="card card-back" transform="translate(36,304)">
      <rect class="card-body" width="66" height="92" rx="1.6"/>
      <rect class="back-art" x="1" y="1" width="64" height="90" rx="1.2" role="img" aria-label="Blue ornamental card back pattern"/>
      <text class="back-name" x="33" y="48" text-anchor="middle">HALLOWELL KIN</text>
    </g>
    <g class="card" transform="translate(114.6,304)">
      <use href="#card-face"/>
      <text class="idx" x="3.5" y="10">A</text><rect class="idx-pip" x="3.5" y="12" width="5" height="5"/>
      <g transform="rotate(180 33 46)"><text class="idx" x="3.5" y="10">A</text><rect class="idx-pip" x="3.5" y="12" width="5" height="5"/></g>
      <rect class="art-red" x="15" y="24" width="36" height="44" rx="4" role="img" aria-label="Ornate filigree diamond, ace of diamonds illustration"/>
    </g>
    <g class="card" transform="translate(193.2,304)">
      <use href="#card-face"/>
      <text class="idx" x="3.5" y="10">K</text><rect class="idx-pip" x="3.5" y="12" width="5" height="5"/>
      <g transform="rotate(180 33 46)"><text class="idx" x="3.5" y="10">K</text><rect class="idx-pip" x="3.5" y="12" width="5" height="5"/></g>
      <rect class="art-red" x="11" y="8" width="44" height="76" rx="2" role="img" aria-label="King of diamonds court illustration"/>
    </g>
    <g class="card" transform="translate(271.8,304)">
      <use href="#card-face"/>
      <text class="idx" x="3.5" y="10">Q</text><rect class="idx-pip" x="3.5" y="12" width="5" height="5"/>
      <g transform="rotate(180 33 46)"><text class="idx" x="3.5" y="10">Q</text><rect class="idx-pip" x="3.5" y="12" width="5" height="5"/></g>
      <rect class="art-red" x="11" y="8" width="44" height="76" rx="2" role="img" aria-label="Queen of diamonds court illustration"/>
    </g>
    <g class="card" transform="translate(350.4,304)">
      <use href="#card-face"/>
      <text class="idx" x="3.5" y="10">J</text><rect class="idx-pip" x="3.5" y="12" width="5" height="5"/>
      <g transform="rotate(180 33 46)"><text class="idx" x="3.5" y="10">J</text><rect class="idx-pip" x="3.5" y="12" width="5" height="5"/></g>
      <rect class="art-red" x="11" y="8" width="44" height="76" rx="2" role="img" aria-label="Jack of diamonds court illustration"/>
    </g>
    <g class="card" transform="translate(429,304)"><use href="#card-face"/><text class="idx" x="2.5" y="10">10</text><rect class="idx-pip" x="3.5" y="12" width="5" height="5"/><g transform="rotate(180 33 46)"><text class="idx" x="2.5" y="10">10</text><rect class="idx-pip" x="3.5" y="12" width="5" height="5"/></g><use class="pips" href="#layout-10"/></g>
    <g class="card" transform="translate(507.6,304)"><use href="#card-face"/><text class="idx" x="3.5" y="10">9</text><rect class="idx-pip" x="3.5" y="12" width="5" height="5"/><g transform="rotate(180 33 46)"><text class="idx" x="3.5" y="10">9</text><rect class="idx-pip" x="3.5" y="12" width="5" height="5"/></g><use class="pips" href="#layout-9"/></g>
    <g class="card" transform="translate(586.2,304)"><use href="#card-face"/><text class="idx" x="3.5" y="10">8</text><rect class="idx-pip" x="3.5" y="12" width="5" height="5"/><g transform="rotate(180 33 46)"><text class="idx" x="3.5" y="10">8</text><rect class="idx-pip" x="3.5" y="12" width="5" height="5"/></g><use class="pips" href="#layout-8"/></g>
    <g class="card" transform="translate(664.8,304)"><use href="#card-face"/><text class="idx" x="3.5" y="10">7</text><rect class="idx-pip" x="3.5" y="12" width="5" height="5"/><g transform="rotate(180 33 46)"><text class="idx" x="3.5" y="10">7</text><rect class="idx-pip" x="3.5" y="12" width="5" height="5"/></g><use class="pips" href="#layout-7"/></g>
    <g class="card" transform="translate(743.4,304)"><use href="#card-face"/><text class="idx" x="3.5" y="10">6</text><rect class="idx-pip" x="3.5" y="12" width="5" height="5"/><g transform="rotate(180 33 46)"><text class="idx" x="3.5" y="10">6</text><rect class="idx-pip" x="3.5" y="12" width="5" height="5"/></g><use class="pips" href="#layout-6"/></g>
    <g class="card" transform="translate(822,304)"><use href="#card-face"/><text class="idx" x="3.5" y="10">5</text><rect class="idx-pip" x="3.5" y="12" width="5" height="5"/><g transform="rotate(180 33 46)"><text class="idx" x="3.5" y="10">5</text><rect class="idx-pip" x="3.5" y="12" width="5" height="5"/></g><use class="pips" href="#layout-5"/></g>
    <g class="card" transform="translate(900.6,304)"><use href="#card-face"/><text class="idx" x="3.5" y="10">4</text><rect class="idx-pip" x="3.5" y="12" width="5" height="5"/><g transform="rotate(180 33 46)"><text class="idx" x="3.5" y="10">4</text><rect class="idx-pip" x="3.5" y="12" width="5" height="5"/></g><use class="pips" href="#layout-4"/></g>
    <g class="card" transform="translate(979.2,304)"><use href="#card-face"/><text class="idx" x="3.5" y="10">3</text><rect class="idx-pip" x="3.5" y="12" width="5" height="5"/><g transform="rotate(180 33 46)"><text class="idx" x="3.5" y="10">3</text><rect class="idx-pip" x="3.5" y="12" width="5" height="5"/></g><use class="pips" href="#layout-3"/></g>
    <g class="card" transform="translate(1057.8,304)"><use href="#card-face"/><text class="idx" x="3.5" y="10">2</text><rect class="idx-pip" x="3.5" y="12" width="5" height="5"/><g transform="rotate(180 33 46)"><text class="idx" x="3.5" y="10">2</text><rect class="idx-pip" x="3.5" y="12" width="5" height="5"/></g><use class="pips" href="#layout-2"/></g>
  </g>

  <!-- Clubs row -->
  <g class="suit-row clubs">
    <g class="card joker" transform="translate(36,413)">
      <use href="#card-face"/>
      <text class="joker-idx" x="3.5" y="6"><tspan x="3.5">J</tspan><tspan x="3.5" dy="4">O</tspan><tspan x="3.5" dy="4">K</tspan><tspan x="3.5" dy="4">E</tspan><tspan x="3.5" dy="4">R</tspan></text>
      <g transform="rotate(180 33 46)"><text class="joker-idx" x="3.5" y="6"><tspan x="3.5">J</tspan><tspan x="3.5" dy="4">O</tspan><tspan x="3.5" dy="4">K</tspan><tspan x="3.5" dy="4">E</tspan><tspan x="3.5" dy="4">R</tspan></text></g>
      <rect class="art-ivory" x="10" y="24" width="44" height="38" rx="3" role="img" aria-label="White jester hat illustration"/>
    </g>
    <g class="card" transform="translate(114.6,413)">
      <use href="#card-face"/>
      <text class="idx" x="3.5" y="10">A</text><rect class="idx-pip" x="3.5" y="12" width="5" height="5"/>
      <g transform="rotate(180 33 46)"><text class="idx" x="3.5" y="10">A</text><rect class="idx-pip" x="3.5" y="12" width="5" height="5"/></g>
      <rect class="art-ivory" x="14" y="24" width="38" height="44" rx="4" role="img" aria-label="Ornate filigree club, ace of clubs illustration"/>
    </g>
    <g class="card" transform="translate(193.2,413)">
      <use href="#card-face"/>
      <text class="idx" x="3.5" y="10">K</text><rect class="idx-pip" x="3.5" y="12" width="5" height="5"/>
      <g transform="rotate(180 33 46)"><text class="idx" x="3.5" y="10">K</text><rect class="idx-pip" x="3.5" y="12" width="5" height="5"/></g>
      <rect class="art-ivory" x="11" y="8" width="44" height="76" rx="2" role="img" aria-label="King of clubs court illustration"/>
    </g>
    <g class="card" transform="translate(271.8,413)">
      <use href="#card-face"/>
      <text class="idx" x="3.5" y="10">Q</text><rect class="idx-pip" x="3.5" y="12" width="5" height="5"/>
      <g transform="rotate(180 33 46)"><text class="idx" x="3.5" y="10">Q</text><rect class="idx-pip" x="3.5" y="12" width="5" height="5"/></g>
      <rect class="art-ivory" x="11" y="8" width="44" height="76" rx="2" role="img" aria-label="Queen of clubs court illustration"/>
    </g>
    <g class="card" transform="translate(350.4,413)">
      <use href="#card-face"/>
      <text class="idx" x="3.5" y="10">J</text><rect class="idx-pip" x="3.5" y="12" width="5" height="5"/>
      <g transform="rotate(180 33 46)"><text class="idx" x="3.5" y="10">J</text><rect class="idx-pip" x="3.5" y="12" width="5" height="5"/></g>
      <rect class="art-ivory" x="11" y="8" width="44" height="76" rx="2" role="img" aria-label="Jack of clubs court illustration"/>
    </g>
    <g class="card" transform="translate(429,413)"><use href="#card-face"/><text class="idx" x="2.5" y="10">10</text><rect class="idx-pip" x="3.5" y="12" width="5" height="5"/><g transform="rotate(180 33 46)"><text class="idx" x="2.5" y="10">10</text><rect class="idx-pip" x="3.5" y="12" width="5" height="5"/></g><use class="pips" href="#layout-10"/></g>
    <g class="card" transform="translate(507.6,413)"><use href="#card-face"/><text class="idx" x="3.5" y="10">9</text><rect class="idx-pip" x="3.5" y="12" width="5" height="5"/><g transform="rotate(180 33 46)"><text class="idx" x="3.5" y="10">9</text><rect class="idx-pip" x="3.5" y="12" width="5" height="5"/></g><use class="pips" href="#layout-9"/></g>
    <g class="card" transform="translate(586.2,413)"><use href="#card-face"/><text class="idx" x="3.5" y="10">8</text><rect class="idx-pip" x="3.5" y="12" width="5" height="5"/><g transform="rotate(180 33 46)"><text class="idx" x="3.5" y="10">8</text><rect class="idx-pip" x="3.5" y="12" width="5" height="5"/></g><use class="pips" href="#layout-8"/></g>
    <g class="card" transform="translate(664.8,413)"><use href="#card-face"/><text class="idx" x="3.5" y="10">7</text><rect class="idx-pip" x="3.5" y="12" width="5" height="5"/><g transform="rotate(180 33 46)"><text class="idx" x="3.5" y="10">7</text><rect class="idx-pip" x="3.5" y="12" width="5" height="5"/></g><use class="pips" href="#layout-7"/></g>
    <g class="card" transform="translate(743.4,413)"><use href="#card-face"/><text class="idx" x="3.5" y="10">6</text><rect class="idx-pip" x="3.5" y="12" width="5" height="5"/><g transform="rotate(180 33 46)"><text class="idx" x="3.5" y="10">6</text><rect class="idx-pip" x="3.5" y="12" width="5" height="5"/></g><use class="pips" href="#layout-6"/></g>
    <g class="card" transform="translate(822,413)"><use href="#card-face"/><text class="idx" x="3.5" y="10">5</text><rect class="idx-pip" x="3.5" y="12" width="5" height="5"/><g transform="rotate(180 33 46)"><text class="idx" x="3.5" y="10">5</text><rect class="idx-pip" x="3.5" y="12" width="5" height="5"/></g><use class="pips" href="#layout-5"/></g>
    <g class="card" transform="translate(900.6,413)"><use href="#card-face"/><text class="idx" x="3.5" y="10">4</text><rect class="idx-pip" x="3.5" y="12" width="5" height="5"/><g transform="rotate(180 33 46)"><text class="idx" x="3.5" y="10">4</text><rect class="idx-pip" x="3.5" y="12" width="5" height="5"/></g><use class="pips" href="#layout-4"/></g>
    <g class="card" transform="translate(979.2,413)"><use href="#card-face"/><text class="idx" x="3.5" y="10">3</text><rect class="idx-pip" x="3.5" y="12" width="5" height="5"/><g transform="rotate(180 33 46)"><text class="idx" x="3.5" y="10">3</text><rect class="idx-pip" x="3.5" y="12" width="5" height="5"/></g><use class="pips" href="#layout-3"/></g>
    <g class="card" transform="translate(1057.8,413)"><use href="#card-face"/><text class="idx" x="3.5" y="10">2</text><rect class="idx-pip" x="3.5" y="12" width="5" height="5"/><g transform="rotate(180 33 46)"><text class="idx" x="3.5" y="10">2</text><rect class="idx-pip" x="3.5" y="12" width="5" height="5"/></g><use class="pips" href="#layout-2"/></g>
  </g>
</svg>
</body>
</html>
```